Alterations to existing business card

Here is my current logo and I want the "cafe and bar" taken off with just the words Lumo and our slogan "Savour the moment" on the card, Plus the logo.
Our Current Business Card is currently 5.5cm by 5.5cm and would like it to remain like this thanks.
The loyalty card can be 10 squares with the logo specifying the 10th coffee free. I would like the cheapest option please.
Also on our business card would like the Facebook logo and instagram Logo with TAZALUMO27 as link to our photos on instagram.

Keep Colour schemes the same please.

On the business cards

Dale Brinton Director
0427916038
dale27lumo@mailvista.test

Paula Ferrisi Principal
0428571963
paulumo@mailvista.test

Thanks Dale

Industry/Entity Type

Business

```html
<!DOCTYPE html>
<html lang="en">
<head>
<meta charset="utf-8">
<title>Lumo – Business Card and Loyalty Card</title>
<link rel="stylesheet" href="https://fonts.googleapis.com/css2?family=Didact+Gothic&display=swap">
<style>
  :root {
    --backdrop: #4a4a4a;
    --card: #ffffff;
    --ink: #111111;
    --ink-soft: #555555;
    --gold: #e8a22c;
    --gold-deep: #c98a1a;
    --band: #000000;
    --band-text: #ffffff;
    --rule: #9a9a9a;
    --stamp-ring: #3a3a3a;
    --stamp-edge: #bdbdbd;
  }
  * { box-sizing: border-box; margin: 0; padding: 0; }
  html, body {
    width: 1105px; height: 1200px; overflow: hidden;
    background: var(--backdrop);
    font-family: "Didact Gothic", "Century Gothic", sans-serif;
  }
  .canvas { position: relative; width: 1105px; height: 1200px; }

  .card {
    position: absolute; width: 449px; height: 449px;
    background: var(--card);
  }
  .card--business { left: 124px; top: 110px; }
  .card--loyalty { left: 500px; top: 630px; }

  .wordmark {
    position: absolute; left: 0; right: 0; text-align: center;
    color: var(--ink); letter-spacing: 3px; line-height: 1; white-space: nowrap;
  }
  .slogan {
    position: absolute; left: 0; right: 0; text-align: center;
    color: var(--gold); letter-spacing: 1.5px; line-height: 1;
    font-style: italic; white-space: nowrap;
  }
  .card--business .wordmark { top: 57px; font-size: 64px; }
  .card--business .slogan { top: 121px; font-size: 14px; }

  .name-band {
    position: absolute; left: 0; right: 0; top: 191px; height: 86px;
    background: var(--band);
  }
  .name-band__mark {
    position: absolute; left: 6px; top: 0; height: 86px; width: 68px;
    display: flex; align-items: center; justify-content: center;
    color: var(--gold); font-size: 17px; letter-spacing: 1px;
  }
  .name-band__name {
    position: absolute; left: 0; right: 0; top: 17px; text-align: center;
    color: var(--gold); font-size: 26px; letter-spacing: 1.5px; padding-left: 8px;
    line-height: 1.2; white-space: nowrap;
  }
  .name-band__role {
    position: absolute; left: 0; right: 0; top: 53px; text-align: center;
    color: var(--band-text); font-size: 19px; letter-spacing: 1px; padding-left: 8px;
    line-height: 1.2;
  }

  .contact {
    position: absolute; left: 0; right: 0; text-align: center;
    color: var(--ink-soft); font-size: 20px; line-height: 1; white-space: nowrap;
  }
  .contact--phone { top: 318px; }
  .contact--email { top: 346px; }

  .social {
    position: absolute; left: 0; right: 0; top: 376px; height: 22px;
    display: flex; align-items: center; justify-content: center; gap: 6px;
  }
  .social__rule { width: 70px; height: 1px; background: var(--rule); }
  .social__dot { width: 19px; height: 19px; border-radius: 50%; background: var(--gold); }
  .social__handle { color: var(--ink-soft); font-size: 18px; letter-spacing: 1px; margin: 0 4px 0 2px; }

  .badge {
    position: absolute; left: 162px; top: 51px; width: 125px; height: 125px;
    border-radius: 50%; border: 3px solid var(--gold);
  }
  .card--loyalty .wordmark { top: 185px; font-size: 52px; }
  .card--loyalty .slogan { top: 236px; font-size: 13px; }

  .stamps { position: absolute; left: 0; top: 0; width: 449px; height: 449px; }
  .stamp__free {
    font-family: "Didact Gothic", "Century Gothic", sans-serif;
    font-size: 17px; fill: var(--ink); stroke: var(--ink); stroke-width: 0.6;
  }
</style>
</head>
<body>
<main class="canvas">

  <section class="card card--business" aria-label="Business card">
    <div class="wordmark">LUMO</div>
    <div class="slogan">SAVOUR THE MOMENT</div>
    <div class="name-band">
      <div class="name-band__mark">LUMO</div>
      <div class="name-band__name">DALE BRINTON</div>
      <div class="name-band__role">DIRECTOR</div>
    </div>
    <div class="contact contact--phone">MOB : 0427916038</div>
    <div class="contact contact--email">dale27lumo@mailvista.test</div>
    <div class="social">
      <span class="social__rule"></span>
      <span class="social__dot"></span>
      <span class="social__dot"></span>
      <span class="social__handle">TAZALUMO27</span>
      <span class="social__rule"></span>
    </div>
  </section>

  <section class="card card--loyalty" aria-label="Loyalty card">
    <div class="badge"></div>
    <div class="wordmark">LUMO</div>
    <div class="slogan">SAVOUR THE MOMENT</div>
    <svg class="stamps" viewBox="0 0 449 449" aria-label="Ten coffee stamps, tenth free">
      <defs>
        <g id="stamp">
          <circle r="32" fill="#fff" stroke="var(--stamp-edge)" stroke-width="2"/>
          <circle r="28" fill="none" stroke="var(--stamp-ring)" stroke-width="2.5"/>
          <path d="M-13 -3 h22 v4 a11 9 0 0 1 -22 0 z" fill="var(--ink)"/>
          <path d="M9 -1 a5 4 0 0 1 0 8" fill="none" stroke="var(--ink)" stroke-width="2.5"/>
          <rect x="-16" y="10" width="28" height="2.5" rx="1" fill="var(--ink)"/>
          <path d="M-6 -7 q-3 -4 0 -8 M0 -7 q-3 -4 0 -8" fill="none" stroke="var(--ink)" stroke-width="1.5"/>
        </g>
      </defs>
      <use href="#stamp" x="72" y="306"/>
      <use href="#stamp" x="147" y="306"/>
      <use href="#stamp" x="222" y="306"/>
      <use href="#stamp" x="297" y="306"/>
      <use href="#stamp" x="372" y="306"/>
      <use href="#stamp" x="72" y="385"/>
      <use href="#stamp" x="147" y="385"/>
      <use href="#stamp" x="222" y="385"/>
      <use href="#stamp" x="297" y="385"/>
      <g class="stamp stamp--free" transform="translate(372 385)">
        <circle r="32" fill="var(--gold)" stroke="var(--gold-deep)" stroke-width="2"/>
        <circle r="28" fill="none" stroke="#ffffff" stroke-opacity="0.5" stroke-width="1.5"/>
        <text class="stamp__free" text-anchor="middle" y="6">FREE</text>
      </g>
    </svg>
  </section>

</main>
</body>
</html>
```